New Business Card Design Project

I need a design for business cards, i am an electrical business called "Corvane Electrical and Communications" i need the cards to be double sided with the company logo on the back (attached) the front needs to say my company name, web site, email address, telephone number, and ABN number and electrical license number. I am open to different arrangements of the information but would like the background to be incorporating something electrical or something that looks smart. open to all additional ideas also.

The company colours are orange and grey see logo attached.

Business Name: Corvane Electrical and Communications
Website: corvaneelectricalandcomms.example.com.au
Email: brent@corvaneelectricalandcomms.example.com.au
Telephone(mobile): 0481209736
ABN: 71208349162
Lic No: 418273D

Target Market(s)

Business entities, Project Managers, Accounts, Clients

Industry/Entity Type

Electrician

Contact Information for Business Card

I need a design for business cards, i am an electrical business called "Corvane Electrical and Communications" i need the cards to be double sided with the company logo on the back (attached) the front needs to say my company name

Font styles to use
Serif
Sans Serif

Colors
f37122
5c5c5c

Requirements
Must have
• Must have the Logo on the back open to different ways of it being on the back but had in mind to keep it central but again open to other options
Nice to have
• A real modern cool background that is eye catching yet contemporary
Should not have
• No backgrounds of a light bulb or plug or anything like that

```html
<!DOCTYPE html>
<html lang="en">
<head>
<meta charset="UTF-8">
<title>Corvane Electrical and Communications – Business Card</title>
<link href="https://fonts.googleapis.com/css2?family=Dosis:wght@300;400;500;600;700&display=swap" rel="stylesheet">
<style>
  :root {
    --orange: #f8a51b;
    --orange-deep: #f39a12;
    --grey-dark: #3f3f41;
    --grey-mid: #5c5c5c;
    --grey-light: #6d6d6f;
    --white: #ffffff;
    --text-soft: #e9e9e9;
    --stage: #e6e4df;
  }
  * { margin: 0; padding: 0; box-sizing: border-box; }
  html, body {
    width: 1200px; height: 950px; overflow: hidden;
    background: var(--stage);
    font-family: "Dosis", sans-serif;
  }
  .canvas {
    position: relative; width: 1200px; height: 950px;
  }
  .card {
    position: absolute; left: 230px; width: 740px; height: 423px;
    border-radius: 28px; overflow: hidden;
    box-shadow: 0 10px 28px rgba(0,0,0,.22);
  }

  /* Front */
  .card-front {
    top: 40px;
    background: var(--orange);
  }
  .front-panel {
    position: absolute; left: 0; right: 0; top: 58px; bottom: 0;
    background: linear-gradient(115deg, var(--grey-light) 0%, var(--grey-mid) 40%, var(--grey-dark) 100%);
  }
  .front-panel::before {
    content: ""; position: absolute; inset: 0;
    background: linear-gradient(155deg, rgba(255,255,255,.16) 0%, rgba(255,255,255,0) 45%);
  }
  .brand {
    position: absolute; left: 58px; top: 92px; color: var(--white);
    font-weight: 500; line-height: 1;
  }
  .brand-name { font-size: 74px; letter-spacing: 6px; }
  .brand-sub { font-size: 15px; letter-spacing: 3.2px; margin-top: 8px; text-transform: uppercase; }
  .person {
    position: absolute; left: 58px; top: 238px; font-size: 25px; font-weight: 600;
  }
  .person-name { color: var(--orange); }
  .person-role { color: var(--white); font-weight: 500; }
  .rule-h {
    position: absolute; left: 40px; top: 286px; width: 460px; height: 1px;
    background: linear-gradient(90deg, rgba(255,255,255,0), rgba(255,255,255,.55) 30%, rgba(255,255,255,.55) 70%, rgba(255,255,255,0));
  }
  .contacts {
    position: absolute; left: 40px; top: 310px; list-style: none;
    color: var(--text-soft); font-size: 16px; line-height: 1.55; letter-spacing: .3px;
  }
  .contacts .label { color: var(--orange); font-weight: 600; }
  .rule-v {
    position: absolute; left: 530px; top: 88px; width: 1px; height: 300px;
    background: linear-gradient(180deg, rgba(255,255,255,0), rgba(255,255,255,.5) 30%, rgba(255,255,255,.5) 70%, rgba(255,255,255,0));
  }
  .registration {
    position: absolute; left: 560px; top: 96px; list-style: none;
    color: var(--text-soft); font-size: 16px; line-height: 1.6; letter-spacing: .4px;
  }

  /* Back */
  .card-back {
    top: 507px;
    background: linear-gradient(160deg, var(--orange) 0%, var(--orange-deep) 100%);
  }
  .back-web {
    position: absolute; left: 42px; top: 34px;
    transform-origin: left top; transform: rotate(90deg) translate(0, -28px);
    color: var(--white); font-size: 17px; letter-spacing: 1.2px; white-space: nowrap;
  }
  .back-brand {
    position: absolute; left: 0; right: 0; top: 50%; transform: translateY(-50%);
    text-align: center; color: var(--white); font-weight: 500; line-height: 1;
  }
  .back-brand .brand-name { font-size: 64px; }
  .back-brand .brand-sub { font-size: 14px; }
</style>
</head>
<body>
<main class="canvas">

  <section class="card card-front" aria-label="Business card front">
    <div class="front-panel"></div>

    <div class="brand">
      <div class="brand-name">CORVANE</div>
      <div class="brand-sub">Electrical &amp; Communications</div>
    </div>

    <p class="person">
      <span class="person-name">Brent Marlowe</span>
      <span class="person-role"> - CEO/Founder</span>
    </p>

    <div class="rule-h"></div>

    <ul class="contacts">
      <li><span class="label">Mobile :</span> 0481209736</li>
      <li>brent@corvaneelectricalandcomms.example.com.au</li>
      <li>corvaneelectricalandcomms.example.com.au</li>
    </ul>

    <div class="rule-v"></div>

    <ul class="registration">
      <li>Lic No: 418273D</li>
      <li>ABN: 71208349162</li>
    </ul>
  </section>

  <section class="card card-back" aria-label="Business card back">
    <p class="back-web">www.corvaneelectricalandcomms.example.com.au</p>
    <div class="back-brand">
      <div class="brand-name">CORVANE</div>
      <div class="brand-sub">Electrical &amp; Communications</div>
    </div>
  </section>

</main>
</body>
</html>
```